Business Card Design for a Personal Trainer

I need a business card design for my job as a personal trainer. It should have a unique, modern and exclusive design. On the front there should be only my logo with my name and my job. 0162/3819204 Tobias Lendhart Wiesengrundweg 14 80417 Munich Germany The most important contact information is the web adress. it can be bigger than the rest, but its not necessary. The card should be 8,5cmx5,5cm big. Font: Roboto. Colors: black, white, gray, 56c1ff.

```html
<!DOCTYPE html>
<html lang="de">
<head>
<meta charset="utf-8">
<title>Tobias Lendhart – Personal Trainer Visitenkarte</title>
<link href="https://fonts.googleapis.com/css2?family=Roboto:wght@300;400;500&display=swap" rel="stylesheet">
<style>
  :root {
    --stage: #2b2522;
    --card-black: #0b0b0b;
    --card-edge: #1a1a1a;
    --white: #f4f4f4;
    --silver: #c9c9c9;
    --gray-band: #4a4a4a;
    --photo-light: #6f6f6f;
    --photo-dark: #1c1c1c;
  }
  * { margin: 0; padding: 0; box-sizing: border-box; }
  html, body { width: 1200px; height: 844px; overflow: hidden; }
  body {
    background: var(--stage);
    font-family: "Roboto", Arial, sans-serif;
    display: flex;
    align-items: center;
    justify-content: center;
    gap: 40px;
  }
  .card {
    position: relative;
    width: 540px;
    height: 350px;
    background: var(--card-black);
    border: 1px solid var(--card-edge);
    overflow: hidden;
  }

  /* Back side: contact details */
  .card-back .bottom-band {
    position: absolute;
    left: 310px; right: 0; bottom: 0;
    height: 36px;
    background: var(--gray-band);
  }
  .card-back .portrait {
    position: absolute;
    left: 70px; bottom: 0;
    width: 240px; height: 228px;
    background: radial-gradient(ellipse at 50% 35%, var(--photo-light), var(--photo-dark) 75%);
  }
  .card-back .identity {
    position: absolute;
    left: 250px; top: 62px;
    width: 268px;
    text-align: center;
    color: var(--white);
  }
  .name {
    font-weight: 300;
    font-size: 29px;
    letter-spacing: 0.5px;
    text-transform: uppercase;
    line-height: 1;
  }
  .role {
    display: flex;
    align-items: center;
    gap: 8px;
    margin-top: 4px;
    font-size: 10px;
    letter-spacing: 4px;
    text-transform: uppercase;
    font-weight: 400;
  }
  .role::before, .role::after {
    content: "";
    flex: 1;
    height: 1px;
    background: currentColor;
  }
  .contacts {
    position: absolute;
    left: 330px; top: 128px;
    list-style: none;
    color: var(--white);
    font-size: 15px;
    font-weight: 300;
    line-height: 21px;
  }
  .contacts li { display: flex; align-items: center; gap: 6px; }
  .contacts svg { width: 14px; height: 14px; flex: none; fill: var(--white); }
  .address {
    position: absolute;
    left: 330px; top: 208px;
    color: var(--white);
    font-size: 15px;
    font-weight: 300;
    line-height: 21px;
    font-style: normal;
  }

  /* Front side: wordmark */
  .card-front .wordmark {
    position: absolute;
    left: 0; right: 0; top: 110px;
    display: flex;
    flex-direction: column;
    align-items: center;
    color: var(--silver);
  }
  .wordmark .mark-square {
    width: 58px; height: 58px;
    border: 3px solid var(--silver);
    margin-bottom: 14px;
  }
  .wordmark .role { width: 200px; margin-top: 5px; }
</style>
</head>
<body>
  <section class="card card-back" aria-label="Rückseite mit Kontaktdaten">
    <div class="bottom-band"></div>
    <div class="portrait" role="img" aria-label="Schwarz-Weiß-Porträt des Trainers mit verschränkten Armen"></div>
    <div class="identity">
      <h1 class="name">Tobias Lendhart</h1>
      <p class="role">Personal Trainer</p>
    </div>
    <ul class="contacts">
      <li><svg viewBox="0 0 16 16" aria-hidden="true"><path d="M3 2h3l1.5 3.5-2 1.2a8 8 0 0 0 3.8 3.8l1.2-2L14 10v3a1 1 0 0 1-1 1A11 11 0 0 1 2 3a1 1 0 0 1 1-1z"/></svg>0162/3819204</li>
      <li><svg viewBox="0 0 16 16" aria-hidden="true"><path d="M1 3h14v10H1zm1.5 1.5v.3L8 9l5.5-4.2v-.3zM2.5 6.6v5h11v-5L8 10.8z"/></svg>t.lendhart@postmail.de</li>
      <li><svg viewBox="0 0 16 16" aria-hidden="true"><circle cx="8" cy="8" r="7"/></svg>www.tobiaslendhart.de</li>
    </ul>
    <address class="address">Wiesengrundweg 14<br>80417 München</address>
  </section>

  <section class="card card-front" aria-label="Vorderseite mit Namenszug">
    <div class="wordmark">
      <div class="mark-square"></div>
      <p class="name">Tobias Lendhart</p>
      <p class="role">Personal Trainer</p>
    </div>
  </section>
</body>
</html>
```